Business Card Design

Business Card for professional consulting firm working with large financial institutions.

Target Market(s)

Executive buyers

Industry/Entity Type

Banking

Contact Information for Business Card

Mild creativity wanted. Not boring, but do elaborate artwork.

Font styles to use
Serif
Sans Serif

Colors

Designer to choose colors to be used in the design.

Requirements
Must have
• Standard business card features - company name, individual name, telephone, website, email, locations.
Nice to have
• Two colors
Should not have
• too many colors, fancy printing, cartoons.

```html
<!DOCTYPE html>
<html lang="en">
<head>
<meta charset="utf-8">
<title>Veldmark Business Card</title>
<link rel="stylesheet" href="https://fonts.googleapis.com/css2?family=Noto+Serif&family=Archivo:wght@400;500&display=swap">
<style>
  :root {
    --stage: #e6e6e8;
    --card-light: #ffffff;
    --card-light-shade: #efefef;
    --card-dark: #2e2e30;
    --ink: #2b2b2b;
    --ink-soft: #4a4a4a;
    --name-grey: #9c9c9c;
    --rule: #555555;
    --mark-light: #d4d4d4;
  }
  * { margin: 0; padding: 0; box-sizing: border-box; }
  html, body {
    width: 1200px; height: 900px; overflow: hidden;
    background: var(--stage);
  }
  .canvas {
    width: 1200px; height: 900px;
    display: flex; flex-direction: column;
    align-items: center; justify-content: center; gap: 40px;
  }
  .card {
    width: 700px; height: 400px;
    border-radius: 26px;
    position: relative;
    box-shadow: 0 6px 18px rgba(0,0,0,0.18);
    overflow: hidden;
  }
  .card-front {
    background: radial-gradient(ellipse at 70% 75%, var(--card-light) 40%, var(--card-light-shade) 100%);
    font-family: "Archivo", sans-serif;
  }
  .card-back {
    background: var(--card-dark);
    display: flex; align-items: center; justify-content: center;
  }
  .person-name {
    position: absolute; left: 42px; top: 104px;
    font-size: 26px; font-weight: 500; letter-spacing: 0.5px;
    color: var(--name-grey); text-transform: uppercase;
  }
  .person-title {
    position: absolute; left: 42px; top: 140px;
    font-size: 16px; color: var(--ink-soft);
  }
  .divider {
    position: absolute; left: 128px; top: 151px;
    width: 520px; height: 1.5px; background: var(--rule);
  }
  .address {
    position: absolute; left: 42px; top: 172px;
    font-size: 16px; line-height: 23px; color: var(--ink);
  }
  .contact-list {
    position: absolute; left: 42px; top: 228px;
    list-style: none; font-size: 16px; line-height: 24px; color: var(--ink);
  }
  .contact-list li { display: flex; align-items: center; gap: 8px; }
  .contact-list svg { width: 12px; height: 12px; flex: none; }
  .brand-name {
    position: absolute; right: 70px; top: 60px;
    font-family: "Noto Serif", serif; font-size: 36px; color: var(--ink);
  }
  .brand-name-back {
    font-family: "Noto Serif", serif; font-size: 64px; color: var(--mark-light);
  }
</style>
</head>
<body>
<main class="canvas">
  <section class="card card-front">
    <div class="brand-name">veldmark</div>
    <div class="person-name">Daniel Hartwell</div>
    <div class="person-title">Director</div>
    <div class="divider"></div>
    <address class="address" style="font-style:normal">27 Larkin St,<br>Wendmoor VIC 3712</address>
    <ul class="contact-list">
      <li>
        <svg viewBox="0 0 12 12" aria-hidden="true"><path d="M3 1 L5 3.5 L4 5 Q5.5 7 7 8 L8.5 7 L11 9 L9.5 11 Q4 10 1 2.5 Z" fill="#999"/></svg>
        +330 5813-4076
      </li>
      <li>
        <svg viewBox="0 0 12 12" aria-hidden="true"><rect x="1" y="2.5" width="10" height="7" fill="none" stroke="#999" stroke-width="1.2"/><path d="M1 2.5 L6 6.5 L11 2.5" fill="none" stroke="#999" stroke-width="1.2"/></svg>
        info@veldmark.com
      </li>
      <li>
        <svg viewBox="0 0 12 12" aria-hidden="true"><circle cx="6" cy="6" r="5" fill="none" stroke="#999" stroke-width="1.2"/><ellipse cx="6" cy="6" rx="2.2" ry="5" fill="none" stroke="#999" stroke-width="1"/><path d="M1 6 H11" stroke="#999" stroke-width="1"/></svg>
        www.veldmark.com
      </li>
    </ul>
  </section>
  <section class="card card-back">
    <div class="brand-name-back">veldmark</div>
  </section>
</main>
</body>
</html>
```